Redesign company trifold brochure

We are rebranding our company in September and looking for a more professional design for our brochure.

What we do - providing interdisciplinary care for those supporting ill, elderly and special needs pets at home following the human hospice model of care - is very novel and our brochure is key in explaining it and our offerings.

We serve dogs and cats. Most of the animals are quite sick, elderly. I have many personal and stock photos we can use in the brochure. Please - no pictures of puppies and/or kittens.

The hard part is fitting the info and message into a clear and concise format.

It must be appealing both to pet owners and vets (who are our primary source of patients through referrals).

It should covey WARMTH, COMPASSION, PROFESSIONALISM, and EXPERTISE.

Please look at our website www.TrellisAnimalRespite.com for more info

We have until now used maroon and copper for colors - to reflect the "sunset" of the pets life. BUT are now changing to Navy, Teal and White to reflect calm, trust and competence.

We will use the same logo recolored.

Existing brochure and new logo are attached.

PLEASE ask questions!!
Updates

We have a library of stock images you are welcome to use. All have been legally acquired and we have the right to use them. You DO NOT have to use them, just sending along in case you wish to. https://www.filecrate.example/sh/qk4vrm82zd1pyno/KLQ7Ztbn-Rrfx2mh9sWpYJ4Dc?dl=0

Our colors are NAVY, TEAL and WHITE. For your reference, the navy we use is 99/87/44/55 (CMYK) The Teal we use is 76/11/44/0 (CMYK) Thank you!

Designers -- pleaseuse pictures of older pets (no puppies or kittens). Below is a link to stock photos we own that would be appropriate for use in the brochure. https://www.filecrate.example/sh/w274m6t9pxkr5da/KLRn3GsfwlTVBXEPcq_8ZNj5u?dl=0 THANK YOU!

Designers -- I would VERY much like to include a photo of a pet in a wheel chair. I have personal photos as well as (purchased) stock photos for this purpose which can be found at http://lnk.example/TARHC-Pets-in-Wheelchairs Thank you!!

Today is the last day! Many of you have submitted beautiful designs and others are rolling in. I am so appreciative of your time and energy!! Please do not let the deadline pass without YOUR very BEST entry being submitted!! Thank you! - Miriam & All of us at Trellis Animal Respite & Home Care

Target Market(s)

Pet Owners and Veterinarians

Industry/Entity Type

Pet Care

Font styles to use
Serif

Colors
0455a3
33b8a4
ffffff

Requirements
Must have
• Our logo and information about our services. Pictures of pets. Our contact info. PLEASE NOTE: this is a 2 sided brochure. Please submit both inside and outside.
Should not have
• puppies, kittens - anything off message

```html
<!DOCTYPE html>
<html lang="en">
<head>
<meta charset="utf-8">
<title>Trellis Animal Respite &amp; Home Care – Brochure Inside</title>
<link href="https://fonts.googleapis.com/css2?family=Courgette&family=Quicksand:wght@500;600;700&display=swap" rel="stylesheet">
<style>
  :root{
    --navy:#0455a3;
    --teal:#33b8a4;
    --white:#ffffff;
    --backdrop:#6f7072;
    --rule:#e6e9ee;
  }
  *{box-sizing:border-box;margin:0;padding:0}
  html,body{width:1200px;height:900px;overflow:hidden;background:var(--backdrop)}
  body{font-family:'Quicksand',sans-serif;color:var(--navy)}
  .brochure{position:absolute;left:60px;top:90px;width:1080px;height:720px;display:flex;box-shadow:0 12px 30px rgba(0,0,0,.35)}
  .panel{position:relative;width:360px;height:720px;background:var(--white);overflow:hidden}
  .panel + .panel{border-left:1px solid var(--rule)}
  .panel-art{position:absolute;inset:0}

  .arrow-list{list-style:none}
  .arrow-list li{position:relative;padding-left:22px}
  .arrow-list li::before{content:"";position:absolute;left:0;top:5px;width:9px;height:6px;border-left:2px solid currentColor;border-bottom:2px solid currentColor;transform:rotate(-45deg)}

  /* panel 1 */
  .intro-text{position:absolute;left:40px;top:290px;width:290px;color:var(--white);font-size:12.5px;line-height:1.35;font-weight:600}
  .intro-title{font-family:'Courgette',cursive;font-size:22px;font-weight:400;margin-bottom:10px;line-height:1.15}
  .intro-text p{margin-bottom:7px}
  .intro-text strong{text-decoration:underline}
  .intro-sub{font-family:'Courgette',cursive;font-size:16px;font-weight:400;margin:6px 0}
  .intro-list li{padding-left:20px;margin-bottom:6px}

  /* panel 2 */
  .services-title{position:absolute;left:40px;top:200px;font-family:'Courgette',cursive;font-size:28px;font-weight:400;color:var(--navy);border-bottom:2px solid var(--navy);padding-bottom:4px;width:280px}
  .services-band{position:absolute;left:0;top:262px;width:330px;background:var(--teal);color:var(--white);font-weight:700;font-size:15px;padding:10px 40px}
  .services-list{position:absolute;left:40px;top:320px;width:280px;font-size:14px;font-weight:600;line-height:1.35}
  .services-list li{margin-bottom:12px}

  /* panel 3 */
  .offer-list{font-size:13.5px;font-weight:600;line-height:1.3}
  .offer-list li{margin-bottom:4px}
  .care-list{position:absolute;left:32px;top:28px;width:300px;color:var(--navy)}
  .extras-heading{position:absolute;left:32px;top:192px;width:300px;font-family:'Courgette',cursive;font-size:19px;font-weight:400;line-height:1.1;color:var(--navy);border-top:2px solid var(--navy);padding-top:8px}
  .extras-list{position:absolute;left:32px;top:250px;width:300px;color:var(--teal)}
  .team-title{position:absolute;left:32px;top:500px;width:230px;font-family:'Courgette',cursive;font-size:28px;font-weight:400;color:var(--navy);border-top:2px solid var(--navy);border-bottom:2px solid var(--navy);padding:2px 0 4px 40px}
  .team-lead{position:absolute;left:32px;top:558px;font-size:19px;font-weight:600;color:var(--teal)}
  .team-intro{position:absolute;left:32px;top:586px;font-size:13px;font-weight:600;color:var(--navy)}
  .team-list{position:absolute;left:32px;top:606px;font-size:13px;font-weight:700;color:var(--navy);list-style:none}
  .team-list li{position:relative;padding-left:16px;margin-bottom:3px}
  .team-list li::before{content:"";position:absolute;left:0;top:5px;width:7px;height:7px;border-radius:50%;background:var(--navy)}
</style>
</head>
<body>
<main class="brochure">

  <section class="panel panel-intro">
    <svg class="panel-art" width="360" height="720" viewBox="0 0 360 720">
      <defs>
        <linearGradient id="photoTone" x1="0" y1="0" x2="1" y2="1">
          <stop offset="0" stop-color="#8aa24a"/>
          <stop offset=".45" stop-color="#d49a4a"/>
          <stop offset="1" stop-color="#a8662a"/>
        </linearGradient>
      </defs>
      <rect width="360" height="600" fill="url(#photoTone)" role="img" aria-label="Photo of a smiling senior golden retriever on grass"/>
      <path d="M0 600 Q180 520 360 560 L360 720 L0 720 Z" fill="var(--white)"/>
      <path d="M0 640 Q180 560 360 600" fill="none" stroke="var(--navy)" stroke-width="1.5"/>
      <circle cx="185" cy="430" r="235" fill="var(--navy)"/>
      <circle cx="185" cy="430" r="245" fill="none" stroke="var(--navy)" stroke-width="1.5"/>
    </svg>
    <div class="intro-text">
      <h2 class="intro-title">Palliative Care and Hospice</h2>
      <p><strong>Palliative Care</strong> seeks to relieve suffering and improve quality of life at all stages of injury and disease, whether curable or not.</p>
      <p><strong>Hospice</strong> is a special kind of Palliative Care focused on pets with a life expectancy of less than one year.</p>
      <h3 class="intro-sub">Both Palliative Care and Hospice:</h3>
      <ul class="intro-list arrow-list">
        <li>Focus on living fully</li>
        <li>Recognize and address all suffering – emotional, social and spiritual</li>
        <li>Use a team approach to meet the needs of the animal and his or her family</li>
        <li>Affirm life while viewing death as a natural, normal process</li>
      </ul>
    </div>
  </section>

  <section class="panel panel-services">
    <svg class="panel-art" width="360" height="720" viewBox="0 0 360 720">
      <circle cx="180" cy="95" r="78" fill="none" stroke="var(--navy)" stroke-width="2"/>
      <circle cx="180" cy="95" r="70" fill="#b98a5a" role="img" aria-label="Round photo of an elderly dog resting"/>
      <path d="M0 640 Q180 600 360 660 L360 720 L0 720 Z" fill="var(--navy)"/>
    </svg>
    <h2 class="services-title">Our Services</h2>
    <p class="services-band">Caring for pets at home</p>
    <ul class="services-list arrow-list">
      <li>In-home comfort care visits</li>
      <li>Pain and symptom management</li>
      <li>Quality of life assessments</li>
      <li>End of life planning</li>
      <li>Caregiver education</li>
    </ul>
  </section>

  <section class="panel panel-team">
    <svg class="panel-art" width="360" height="720" viewBox="0 0 360 720">
      <path d="M360 610 Q345 690 230 720 L360 720 Z" fill="var(--navy)"/>
      <path d="M352 610 Q336 686 210 720" fill="none" stroke="var(--navy)" stroke-width="1.5"/>
    </svg>
    <ul class="care-list offer-list arrow-list">
      <li>Coordination of care with your vet and other care professionals</li>
      <li>Home cooked meals and treats</li>
      <li>Transportation and errand running</li>
      <li>Equipment and supplies</li>
      <li>Funerals and memorials</li>
      <li>Bereavement support</li>
    </ul>
    <h3 class="extras-heading">Our skilled team members can also provide:</h3>
    <ul class="extras-list offer-list arrow-list">
      <li>Bereavement support</li>
      <li>Cold LASER Treatments</li>
      <li>Reiki</li>
      <li>Passive Range of Motion (PROM)</li>
      <li>Rehabilitation Support</li>
      <li>Grooming</li>
      <li>Essential Oils</li>
      <li>Bach Flower Essences</li>
      <li>Aroma Therapy</li>
      <li>Music Therapy</li>
      <li>Pet Therapy</li>
    </ul>
    <h2 class="team-title">Our Team</h2>
    <p class="team-lead">Lead by Miriam Castell, C.T.</p>
    <p class="team-intro">our interdisciplinary team includes:</p>
    <ul class="team-list">
      <li>Certified Thanatologi</li>
      <li>Certified Veterinary Technicians</li>
    </ul>
  </section>

</main>
</body>
</html>
```